Brand Identity Stationary Package

Hello I'm looking for a full branding package for my Property Management Company. I have a logo but looking to have the following
Business Card
Email signature
Facebook cover photo
Letterhead (word.doc)
#10 Envelope
Pocket Folder - link to 9x12 pocket folder design specs https://www.printorbit-example.ca/marketing-materials/presentation-folders
would like everything to match and be brand identifiable. The company looks after residential properties/apartments and some commercial properties. Attached is a zip of the files.
For Business Card
Name: Gareth Lindqvist
Position: Operations Manager
Number: 1 (555) 384-2917
Email: Gareth@harborkey-example.ca
Website: Harborkey-example.ca
Property Management

```html
<!DOCTYPE html>
<html lang="en">
<head>
<meta charset="utf-8">
<title>Harborkey Property Management – #10 Envelope</title>
<link rel="stylesheet" href="https://fonts.googleapis.com/css2?family=Montserrat:wght@600;700&family=Source+Sans+3:wght@400&display=swap">
<style>
  :root {
    --brand-green: #80a642;
    --ink: #141414;
    --paper: #f4f3f3;
    --paper-light: #fbfbfb;
    --backdrop: #d2d2d2;
    --white: #ffffff;
  }
  * { margin: 0; padding: 0; box-sizing: border-box; }
  html, body {
    width: 1200px; height: 1050px; overflow: hidden;
    background: var(--backdrop);
  }
  .sheet { position: relative; width: 1200px; height: 1050px; }
  .envelope {
    position: absolute; left: 145px; width: 910px; height: 390px;
    background: radial-gradient(ellipse at 50% 60%, var(--paper-light) 0%, var(--paper) 70%);
    overflow: hidden;
  }
  .envelope--back { top: 105px; }
  .envelope--front { top: 555px; }
  .envelope__art { position: absolute; inset: 0; width: 910px; height: 390px; }
  .wordmark {
    position: absolute;
    font-family: "Montserrat", sans-serif; font-weight: 700;
    letter-spacing: 0.09em; line-height: 1;
  }
  .tagline {
    position: absolute;
    font-family: "Montserrat", sans-serif; font-weight: 600;
    font-size: 10.5px; letter-spacing: 0.72em; line-height: 1;
  }
  .envelope--back .wordmark {
    top: 35px; left: 0; right: 0; text-align: center;
    font-size: 44px; color: var(--white);
  }
  .envelope--back .tagline {
    top: 80px; left: 0; right: 0; text-align: center;
    color: var(--white); padding-left: 0.72em;
  }
  .envelope--front .wordmark {
    top: 113px; left: 33px; font-size: 36px; color: var(--ink);
  }
  .envelope--front .tagline {
    top: 156px; left: 34px; color: var(--ink); font-size: 9.5px;
  }
  .contact-list {
    position: absolute; top: 196px; left: 33px; list-style: none;
    font-family: "Source Sans 3", sans-serif; font-size: 20px; color: var(--ink);
  }
  .contact-list li { display: flex; align-items: center; height: 26px; }
  .contact-list svg { width: 16px; height: 16px; margin-right: 13px; fill: var(--brand-green); }
</style>
</head>
<body>
<main class="sheet">

  <section class="envelope envelope--back" aria-label="Envelope back with flap">
    <svg class="envelope__art" viewBox="0 0 910 390" aria-hidden="true">
      <path d="M0,0 H910 L884,90 Q870,131 820,131 H90 Q40,131 26,90 Z" fill="var(--brand-green)"/>
    </svg>
    <div class="wordmark">HARBORKEY</div>
    <div class="tagline">PROPERTY MANAGEMENT</div>
  </section>

  <section class="envelope envelope--front" aria-label="Envelope front with return address">
    <svg class="envelope__art" viewBox="0 0 910 390" aria-hidden="true">
      <path d="M0,0 H910 V78 Q455,40 0,78 Z" fill="var(--brand-green)"/>
      <path d="M0,94 Q380,52 730,70 Q380,60 0,86 Z" fill="var(--ink)"/>
      <path d="M0,390 H910 V340 Q455,385 0,340 Z" fill="var(--brand-green)"/>
      <path d="M910,326 Q560,358 180,349 Q560,357 910,338 Z" fill="var(--ink)"/>
    </svg>
    <div class="wordmark">HARBORKEY</div>
    <div class="tagline">PROPERTY MANAGEMENT</div>
    <ul class="contact-list">
      <li>
        <svg viewBox="0 0 16 16" aria-hidden="true"><path d="M1,6 Q8,0 15,6 L13,8 L11,6 H5 L3,8 Z M3,9 L5,7 H11 L13,9 V14 H3 Z"/></svg>
        1 (555) 384-2917
      </li>
      <li>
        <svg viewBox="0 0 16 16" aria-hidden="true"><path d="M1,3 H15 L8,9 Z M1,5 L8,11 L15,5 V13 H1 Z"/></svg>
        Gareth@harborkey-example.ca
      </li>
      <li>
        <svg viewBox="0 0 16 16" aria-hidden="true"><circle cx="8" cy="8" r="7.5"/><path d="M4,4 Q7,5 6,8 Q4,9 5,12 Q2,10 3,6 Z M10,3 Q13,5 12,9 Q10,8 10,3 Z" fill="var(--white)"/></svg>
        www.Harborkey-example.ca
      </li>
    </ul>
  </section>

</main>
</body>
</html>
```